Irrigation Business needs their business cards modernised and revamped

I would like to keep my current logo, colours and revamp the format of the card.

I would like the card to be clean yet important.

Im not sure if you include texture but i would like the named logo to be indented into the card etc.

show me something alive and free something thats clinical to the point yet has a feel of achievement. i would like people to go nice card.

Target Market(s)

high end clients, corporate, sports field manger, the guys that make the decisions

Industry/Entity Type

Business

Contact Information for Business Card

nformation to be included

Dean Harlow (Director)
0487305526
dean@kolvat.biz
www.kestonfieldworks.com

instagram logo
google logo
facebook logo

Colors

Designer to choose colors to be used in the design.

Requirements
Nice to have
• indentations a really nice feel to the card good texture

```html
<!DOCTYPE html>
<html lang="en">
<head>
<meta charset="utf-8">
<title>Keston Fieldworks — Business Cards</title>
<link rel="stylesheet" href="https://fonts.googleapis.com/css2?family=Roboto+Condensed:wght@700&family=Roboto:wght@400;500&display=swap">
<style>
  :root {
    --backdrop: #242424;
    --paper: #f3f3f3;
    --brand-blue: #2f5fa5;
    --brand-green: #2ea24f;
    --rule-blue: #3aa0d8;
    --ink: #444444;
    --back-blue-top: #4677b3;
    --back-blue-bottom: #3a69a6;
    --white: #ffffff;
  }
  * { box-sizing: border-box; margin: 0; padding: 0; }
  html, body { width: 1200px; height: 960px; overflow: hidden; }
  body {
    background: var(--backdrop);
    position: relative;
    font-family: "Roboto", Arial, sans-serif;
  }
  .card {
    position: absolute;
    width: 600px;
    height: 343px;
    box-shadow: 0 3px 8px rgba(0,0,0,.55);
    overflow: hidden;
  }
  /* Front */
  .card-front { left: 314px; top: 113px; background: var(--paper); }
  .brand-mark {
    position: absolute;
    left: 415px; top: 30px;
    width: 80px; height: 80px;
    border-radius: 50%;
    background: var(--brand-blue);
  }
  .brand-name {
    position: absolute;
    right: 35px; top: 116px;
    font-family: "Roboto Condensed", Arial, sans-serif;
    font-weight: 700;
    font-size: 25px;
    color: var(--brand-blue);
    letter-spacing: .2px;
  }
  .holder { position: absolute; left: 35px; top: 192px; }
  .holder-name {
    font-family: "Roboto Condensed", Arial, sans-serif;
    font-weight: 700;
    font-size: 22px;
    color: var(--brand-blue);
    line-height: 26px;
  }
  .holder-role {
    font-size: 15px;
    font-weight: 500;
    color: var(--brand-green);
    margin-top: 4px;
  }
  .divider {
    position: absolute;
    left: 35px; top: 244px;
    width: 530px; height: 1px;
    background: var(--rule-blue);
  }
  .contacts {
    position: absolute;
    left: 35px; top: 256px;
    list-style: none;
  }
  .contacts li {
    display: flex;
    align-items: center;
    gap: 8px;
    font-size: 14.5px;
    color: var(--ink);
    height: 19px;
  }
  .contacts svg { width: 13px; height: 13px; fill: var(--brand-blue); flex: none; }
  /* Back */
  .card-back {
    left: 311px; top: 472px;
    background: linear-gradient(180deg, var(--back-blue-top), var(--back-blue-bottom));
  }
  .back-emblem {
    position: absolute;
    left: 262px; top: 8px;
    width: 330px; height: 330px;
    border-radius: 50%;
    background: rgba(255,255,255,.09);
  }
  .back-brand {
    position: absolute;
    left: 28px; top: 234px;
    width: 220px;
    text-align: center;
    font-family: "Roboto Condensed", Arial, sans-serif;
    font-weight: 700;
    font-size: 23px;
    color: var(--white);
  }
  .social-row {
    position: absolute;
    left: 35px; top: 287px;
    width: 200px; height: 28px;
    display: flex; align-items: center; justify-content: center; gap: 6px;
  }
  .social-row .rule {
    width: 52px; height: 1px;
    background: linear-gradient(90deg, rgba(255,255,255,0), rgba(255,255,255,.8));
  }
  .social-row .rule.right {
    background: linear-gradient(90deg, rgba(255,255,255,.8), rgba(255,255,255,0));
  }
  .social-dot {
    width: 27px; height: 27px;
    border-radius: 50%;
    background: var(--white);
  }
</style>
</head>
<body>
  <section class="card card-front">
    <div class="brand-mark"></div>
    <div class="brand-name">KESTON FIELDWORKS</div>

    <div class="holder">
      <div class="holder-name">DEAN HARLOW</div>
      <div class="holder-role">DIRECTOR</div>
    </div>
    <div class="divider"></div>

    <ul class="contacts">
      <li>
        <svg viewBox="0 0 24 24"><path d="M6.6 10.8a15.1 15.1 0 0 0 6.6 6.6l2.2-2.2c.3-.3.7-.4 1-.2 1.1.4 2.3.6 3.6.6.6 0 1 .4 1 1V20c0 .6-.4 1-1 1A17 17 0 0 1 3 4c0-.6.4-1 1-1h3.5c.6 0 1 .4 1 1 0 1.3.2 2.5.6 3.6.1.3 0 .7-.2 1z"/></svg>
        0487305526
      </li>
      <li>
        <svg viewBox="0 0 24 24"><path d="M2 5h20v14H2z M2 5l10 8 10-8" fill="none" stroke="#2f5fa5" stroke-width="0"/><path d="M2 6.5 12 13l10-6.5V19H2z"/><path d="M2 5h20l-10 6.5z"/></svg>
        dean@kolvat.biz
      </li>
      <li>
        <svg viewBox="0 0 24 24"><circle cx="12" cy="12" r="10"/><path d="M2 12h20M12 2c3 3 3 17 0 20M12 2c-3 3-3 17 0 20" fill="none" stroke="#f3f3f3" stroke-width="1.5"/></svg>
        www.kestonfieldworks.com
      </li>
    </ul>
  </section>

  <section class="card card-back">
    <div class="back-emblem"></div>
    <div class="back-brand">KESTON FIELDWORKS</div>
    <div class="social-row">
      <span class="rule"></span>
      <span class="social-dot"></span>
      <span class="social-dot"></span>
      <span class="social-dot"></span>
      <span class="rule right"></span>
    </div>
  </section>
</body>
</html>
```